E learning Platform for privacy

Current website is as below and its more of a shell.
I need someone to take the text and content and design it properly.
https://study.vornaquill.com/

After that, design has to be implemented with elementor and wordpress
https://elementor.com/

```html
<!DOCTYPE html>
<html lang="en">
<head>
<meta charset="utf-8">
<title>Vornaquill Learning Centre</title>
<link rel="stylesheet" href="https://fonts.googleapis.com/css2?family=Montserrat:wght@800;900&family=Poppins:wght@300;400;500;600&display=swap">
<style>
:root{
  --orange:#f0901e;
  --orange-deep:#ea741b;
  --ink:#1f1f1f;
  --text:#555;
  --muted:#777;
  --line:#e6e6e6;
  --paper:#ffffff;
  --grey:#f1f1f1;
}
*{box-sizing:border-box;margin:0;padding:0}
html,body{width:1200px;height:4568px;overflow:hidden}
body{position:relative;background:var(--paper);font-family:"Poppins",sans-serif;color:var(--ink)}
.abs{position:absolute}
.accent{color:var(--orange)}
.btn{position:absolute;display:flex;align-items:center;justify-content:center;gap:14px;background:linear-gradient(90deg,var(--orange),var(--orange-deep));color:#fff;font-size:15px;font-weight:600;border-radius:10px;text-transform:uppercase}
.btn svg{width:32px;height:12px}
.ph{position:absolute}
.brand{position:absolute;left:76px;top:14px;font-weight:500;font-size:34px;letter-spacing:2px;color:var(--orange);line-height:1}
.brand small{display:block;font-size:8px;letter-spacing:5px;color:#444;margin-top:6px;font-weight:500}
.nav{position:absolute;top:32px;left:461px;display:flex;gap:24px;font-size:14px;font-weight:500;color:#222}
.nav .on{color:var(--orange)}
.register{left:1008px;top:23px;width:114px;height:39px;font-size:14px;font-weight:500;border-radius:8px}
.hero-title{left:76px;top:236px;font-family:"Montserrat",sans-serif;font-weight:900;font-size:53px;line-height:57px;letter-spacing:1px}
.hero-sub{left:77px;top:420px;font-size:20px;line-height:27px;color:#555;font-weight:300}
.sec-title{font-size:38px;font-weight:500;line-height:1.2}
.para{font-size:14px;line-height:27px;color:var(--text)}
.card{position:absolute;top:1352px;width:313px;height:397px;background:#fff;box-shadow:0 2px 14px rgba(0,0,0,.1)}
.card .pic{position:absolute;left:0;top:0;width:313px;height:208px}
.card .free{position:absolute;right:12px;top:178px;width:64px;height:64px;border-radius:50%;background:linear-gradient(135deg,var(--orange),var(--orange-deep));color:#fff;font-size:15px;font-weight:500;display:flex;align-items:center;justify-content:center}
.card h3{position:absolute;left:22px;top:234px;font-size:20px;font-weight:500;line-height:25px}
.card .meta{position:absolute;left:22px;font-size:13px;color:#555;display:flex;align-items:center;gap:10px}
.feat h4{position:absolute;font-size:20px;font-weight:500;line-height:25px;color:#222}
.feat p{position:absolute;font-size:14px;line-height:24.5px;color:#666}
.ring{position:absolute;width:82px;height:82px;border-radius:50%;border:2px solid var(--orange);background:#fff;display:flex;align-items:center;justify-content:center}
.ring.inv{border-color:#fff;background:transparent}
.fcol h5{position:absolute;font-size:19px;font-weight:600;color:#222}
.fcol li{position:absolute;list-style:none;font-size:14px;color:#555;padding-left:20px}
.fcol li::before{content:"";position:absolute;left:0;top:8px;width:5px;height:5px;border-radius:50%;background:var(--orange)}
</style>
</head>
<body>

<div class="brand">VORNAQUILL<small>LEARNING CENTRE</small></div>
<nav class="nav">
  <span class="on">HOME</span><span>BLOGS</span><span>COURSES</span><span>ABOUT US</span><span>CONTACT US</span><span>LOGIN</span>
</nav>
<div class="btn register">REGISTER</div>

<h1 class="abs hero-title">Data<br>Privacy<br><span class="accent">Mastery</span></h1>
<p class="abs hero-sub">Largest online e-learning resource for<br>data protection &amp; privacy</p>
<div class="btn" style="left:76px;top:494px;width:199px;height:50px">Get Trained
  <svg viewBox="0 0 32 12"><path d="M0 6h30M25 1l5 5-5 5" stroke="#fff" stroke-width="1.6" fill="none"/></svg></div>
<svg class="abs" style="left:550px;top:89px" width="650" height="585" viewBox="0 0 650 585">
  <path d="M330 0 H 0 V 210 A 190 190 0 0 0 190 400 V 290 H 330 Z" fill="#f4a94e"/>
  <path d="M650 170 V 585 H 200 A 190 190 0 0 1 200 205 H 650 Z" fill="#f0901e"/>
  <path d="M30 290 L 250 260 L 320 80 C 360 60 440 70 470 130 C 520 220 600 250 600 320 L 420 560 L 320 570 Z" fill="#d8c2a8" role="img" aria-label="Photo of a smiling student working on a laptop"/>
</svg>

<svg class="ph" style="left:0;top:727px" width="438" height="487" viewBox="0 0 438 487" role="img" aria-label="Photo of a young woman studying at a desk">
  <defs><linearGradient id="g1" x1="0" x2="1" y1="0" y2="1"><stop offset="0" stop-color="#e4ded6"/><stop offset="1" stop-color="#b9aea3"/></linearGradient></defs>
  <path d="M0 60 C 120 -20 300 -10 390 90 C 470 190 440 380 300 440 C 200 480 80 490 0 487 Z" fill="url(#g1)"/>
</svg>
<p class="abs" style="left:551px;top:797px;font-size:20px;font-weight:500">Welcome To</p>
<h2 class="abs sec-title accent" style="left:551px;top:826px">(VORNAQUILL)</h2>
<h2 class="abs sec-title" style="left:551px;top:873px">Learning Centre</h2>
<p class="abs para" style="left:555px;top:941px;width:400px">Lorem Ipsum is simply dummy text of the printing and typesetting industry. Lorem Ipsum has been the industry's standard dummy text ever since the 1500s, when an unknown printer took a galley of type and scrambled it to make a type specimen book. It has survived not only five</p>
<div class="btn" style="left:555px;top:1117px;width:198px;height:50px">Learn More
  <svg viewBox="0 0 32 12"><path d="M0 6h30M25 1l5 5-5 5" stroke="#fff" stroke-width="1.6" fill="none"/></svg></div>

<h2 class="abs sec-title" style="left:0;width:1200px;text-align:center;top:1270px"><span class="accent">Featured</span> Courses</h2>
<div class="card" style="left:277px">
  <div class="pic" role="img" aria-label="Photo of hands on a laptop and a printed chart" style="background:linear-gradient(135deg,#9fb4c4,#dfe5ea)"></div>
  <div class="free">FREE</div>
  <h3>How to Scale Social<br>Impact</h3>
  <div class="meta" style="top:297px"><svg width="12" height="12" viewBox="0 0 12 12"><rect x="1" y="2" width="10" height="9" fill="none" stroke="#f0901e"/><path d="M1 5h10" stroke="#f0901e"/></svg>Dec 19,2019</div>
  <div class="meta" style="top:329px"><svg width="12" height="12" viewBox="0 0 12 12"><circle cx="6" cy="3.5" r="3" fill="#f0901e"/><path d="M0 12a6 5 0 0 1 12 0z" fill="#f0901e"/></svg>Mr.Example</div>
  <div class="abs" style="left:24px;bottom:0;width:48px;height:3px;background:var(--orange)"></div>
</div>
<div class="card" style="left:610px">
  <div class="pic" role="img" aria-label="Photo of a man with headphones taking notes" style="background:linear-gradient(135deg,#7f98ad,#c9d2d9)"></div>
  <div class="free">FREE</div>
  <h3>Global Social<br>Enrepreneurship</h3>
  <div class="meta" style="top:299px"><svg width="12" height="12" viewBox="0 0 12 12"><rect x="1" y="2" width="10" height="9" fill="none" stroke="#f0901e"/><path d="M1 5h10" stroke="#f0901e"/></svg>Dec 18,2019</div>
  <div class="meta" style="top:331px"><svg width="12" height="12" viewBox="0 0 12 12"><circle cx="6" cy="3.5" r="3" fill="#f0901e"/><path d="M0 12a6 5 0 0 1 12 0z" fill="#f0901e"/></svg>Mr.Example</div>
</div>

<h2 class="abs sec-title" style="left:78px;top:1834px;line-height:47px">Why The <span class="accent">(VORNAQUILL)</span> Learning<br>Centre?</h2>
<p class="abs" style="left:78px;top:1938px;font-size:14px;line-height:26px;color:#555;width:540px">Our mission at the Vornaquill Learning Centre for data privacy training is to provide business and job opportunities.</p>
<div class="abs" style="left:0;top:2024px;width:760px;height:447px;background:linear-gradient(90deg,#ececec,#f7f7f7)" role="img" aria-label="Faded photo of a study room"></div>
<div class="abs" style="left:760px;top:2024px;width:440px;height:447px;background:var(--orange)"></div>
<div class="feat">
  <div class="ring" style="left:78px;top:2083px"><svg width="40" height="40" viewBox="0 0 40 40" fill="none" stroke="#f0901e" stroke-width="4"><path d="M6 6l28 28M34 6L6 34M6 6h9M6 6v9M34 34h-9M34 34v-9M34 6h-9M34 6v9M6 34h9M6 34v-9"/></svg></div>
  <h4 style="left:183px;top:2081px">Comprehensive<br>Roadmap</h4>
  <p style="left:185px;top:2142px">Our objective is to provide a<br>comprehensive competency<br>roadmap, instead.</p>
  <div class="ring" style="left:432px;top:2083px"><svg width="42" height="42" viewBox="0 0 42 42"><circle cx="21" cy="21" r="15" fill="none" stroke="#f0901e" stroke-width="6" stroke-dasharray="5 4"/><circle cx="21" cy="21" r="7" fill="#f0901e"/></svg></div>
  <h4 style="left:537px;top:2081px">Operational<br>Perspective</h4>
  <p style="left:539px;top:2142px">We cover a broad range of<br>data protection topics from<br>both a legal and.</p>
  <div class="ring inv" style="left:790px;top:2083px"><svg width="40" height="44" viewBox="0 0 40 44"><circle cx="20" cy="15" r="12" fill="#111"/><circle cx="20" cy="15" r="6" fill="#f0901e"/><path d="M12 24l-4 16 7-3 4 6 1-15M28 24l4 16-7-3-4 6-1-15" fill="#111"/></svg></div>
  <h4 style="left:896px;top:2081px;color:#fff">Academic &amp; Internatio<br>-nal Certification</h4>
  <p style="left:898px;top:2142px;color:#fff">We partner with prominent<br>universities in the region as<br>well as international.</p>

  <div class="ring" style="left:78px;top:2281px"><svg width="40" height="40" viewBox="0 0 40 40"><path d="M4 12h10a5 5 0 1 1 10 0h10v10a5 5 0 1 0 0 10v6H4V26a5 5 0 1 0 0-10z" fill="#f0901e"/></svg></div>
  <h4 style="left:183px;top:2280px">Modular Approach<br>&amp; Flexibility</h4>
  <p style="left:185px;top:2341px">All our courses are modular in<br>nature to cater to the busy<br>professional, meaning.</p>
  <div class="ring" style="left:432px;top:2281px"><svg width="42" height="42" viewBox="0 0 42 42" fill="#f0901e"><circle cx="12" cy="8" r="5"/><path d="M5 16h14v12h-3v12h-8V28H5z"/><circle cx="29" cy="17" r="4"/><path d="M23 24h12v9h-3v7h-6v-7h-3z"/></svg></div>
  <h4 style="left:537px;top:2280px">Network With<br>Other Peers</h4>
  <p style="left:539px;top:2341px">Participate in our online<br>communities and discussion<br>rooms and your .</p>
  <div class="ring inv" style="left:790px;top:2281px"><svg width="40" height="36" viewBox="0 0 40 36"><rect x="2" y="8" width="36" height="26" rx="4" fill="#111"/><path d="M14 8V3h12v5" stroke="#111" stroke-width="3" fill="none"/><rect x="17" y="17" width="6" height="5" fill="#f0901e"/></svg></div>
  <h4 style="left:896px;top:2280px;color:#fff">Business and Job<br>Opportunities</h4>
  <p style="left:898px;top:2341px;color:#fff">Collaborate with other<br>professionals on potential<br>business opportunities.</p>
</div>

<h2 class="abs sec-title" style="left:156px;top:2620px">What <span class="accent">People</span> Say</h2>
<svg class="abs" style="left:160px;top:2700px" width="56" height="48" viewBox="0 0 56 48" fill="#f0901e"><path d="M2 46V26C2 12 8 4 22 0l2 6c-8 3-11 8-11 14h11v26zM32 46V26C32 12 38 4 52 0l2 6c-8 3-11 8-11 14h11v26z"/></svg>
<p class="abs" style="left:151px;top:2782px;width:430px;font-size:15px;line-height:29.5px;color:#555">" Lorem Ipsum is simply dummy text of the printing and typesetting industry. Lorem Ipsum has been the industry's standard dummy text ever since the 1500s, when an unknown printer took a "</p>
<div class="abs" style="left:156px;top:2931px;width:18px;height:3px;background:var(--orange)"></div>
<p class="abs accent" style="left:184px;top:2918px;font-size:19px;font-weight:500">Client Name</p>
<svg class="ph" style="left:760px;top:2544px" width="440" height="475" viewBox="0 0 440 475" role="img" aria-label="Photo of a smiling woman, client portrait">
  <path d="M200 20 C 300 -10 420 20 440 40 V 475 H 230 C 90 470 0 380 0 240 C 0 120 90 50 200 20 Z" fill="#cfc7bf"/>
</svg>
<svg class="abs" style="left:860px;top:2974px" width="104" height="46" viewBox="0 0 104 46">
  <circle cx="23" cy="23" r="23" fill="#f0901e"/><path d="M27 15l-8 8 8 8" stroke="#fff" stroke-width="2" fill="none"/>
  <circle cx="80" cy="23" r="23" fill="#ea741b"/><path d="M76 15l8 8-8 8" stroke="#fff" stroke-width="2" fill="none"/>
</svg>

<div class="abs" style="left:0;top:3075px;width:601px;height:417px;background:var(--orange)"></div>
<div class="abs" style="left:601px;top:3075px;width:599px;height:417px;background:linear-gradient(90deg,#f0f0f0,#fafafa)" role="img" aria-label="Faded photo of a library"></div>
<h2 class="abs" style="left:78px;top:3115px;font-size:42px;line-height:48px;font-weight:500;color:#222">SignUp For<br><span style="color:#fff">Newsletter !</span></h2>
<p class="abs" style="left:78px;top:3225px;font-size:14px;line-height:25px;color:#fff;width:440px">Subscribe now &amp; receive weekly newsletter with educational materials, new courses, interesting posts, popular books &amp; much more!</p>
<div class="abs" style="left:76px;top:3316px;width:429px;height:52px;background:#fff;display:flex;align-items:center;justify-content:space-between;padding:0 18px;font-size:13px;color:#777">Enter Email *
  <svg width="14" height="10" viewBox="0 0 14 10"><rect width="14" height="10" fill="#f0901e"/><path d="M0 0l7 6 7-6" stroke="#fff" fill="none"/></svg></div>
<div class="btn" style="left:76px;top:3382px;width:188px;height:50px;background:var(--orange-deep)">Subscribe
  <svg viewBox="0 0 32 12"><path d="M0 6h30M25 1l5 5-5 5" stroke="#fff" stroke-width="1.6" fill="none"/></svg></div>

<svg class="abs" style="left:698px;top:3140px" width="64" height="40" viewBox="0 0 64 40" fill="#f0901e"><circle cx="32" cy="10" r="8"/><path d="M18 38c0-12 6-18 14-18s14 6 14 18z"/><circle cx="13" cy="14" r="6"/><path d="M1 36c0-9 5-13 12-13 3 0 5 1 7 2-3 3-5 7-5 11z"/><circle cx="51" cy="14" r="6"/><path d="M63 36c0-9-5-13-12-13-3 0-5 1-7 2 3 3 5 7 5 11z"/></svg>
<p class="abs" style="left:789px;top:3128px;font-size:42px;font-weight:600">6,375</p>
<p class="abs" style="left:792px;top:3182px;font-size:15px;color:#333">Enrolled Student</p>
<svg class="abs" style="left:698px;top:3250px" width="64" height="50" viewBox="0 0 64 50" fill="#f0901e"><path d="M2 4h24v20H2zM30 4h24v20H30z" opacity=".9"/><path d="M36 28l14-6 14 6-14 6z"/><path d="M42 32v8c4 3 12 3 16 0v-8l-8 4z"/></svg>
<p class="abs" style="left:789px;top:3245px;font-size:42px;font-weight:600">144</p>
<p class="abs" style="left:792px;top:3299px;font-size:15px;color:#333">Lessons</p>
<svg class="abs" style="left:700px;top:3367px" width="66" height="36" viewBox="0 0 66 36" fill="#f0901e"><rect x="0" y="2" width="44" height="32" rx="5"/><path d="M46 18l20-14v28z"/><path d="M17 11l12 7-12 7z" fill="#fff"/></svg>
<p class="abs" style="left:789px;top:3355px;font-size:42px;font-weight:600">169</p>
<p class="abs" style="left:792px;top:3409px;font-size:15px;color:#333">Videos</p>

<h2 class="abs sec-title" style="left:0;width:1200px;text-align:center;top:3551px">Latest <span class="accent">Blog</span></h2>
<div class="abs" style="left:163px;top:3644px;width:519px;height:436px;background:linear-gradient(160deg,#3d4d5c,#1b242d)" role="img" aria-label="Photo of a man with headphones smiling at a laptop"></div>
<p class="abs" style="left:203px;top:3987px;font-size:26px;font-weight:500;color:#fff">How to write blog</p>
<p class="abs accent" style="left:205px;top:4030px;font-size:15px">December 18, 2019</p>
<div class="abs" style="left:704px;top:3644px;width:333px;height:208px;background:linear-gradient(160deg,#f0a04a,#e58a26)" role="img" aria-label="Orange-tinted photo of a woman in a library"></div>
<p class="abs" style="left:725px;top:3770px;font-size:22px;font-weight:500;color:#fff">How to write blog</p>
<p class="abs" style="left:727px;top:3806px;font-size:14px;color:#fff">December 18, 2019</p>
<div class="abs" style="left:704px;top:3873px;width:333px;height:207px;background:linear-gradient(160deg,#f0a04a,#e58a26)" role="img" aria-label="Orange-tinted photo of a student reading"></div>
<p class="abs" style="left:725px;top:4008px;font-size:22px;font-weight:500;color:#fff">Hello world!</p>
<p class="abs" style="left:727px;top:4046px;font-size:14px;color:#fff">December 13, 2019</p>

<div class="abs" style="left:0;top:4151px;width:1200px;height:417px;background:var(--grey)"></div>
<svg class="abs" style="left:0;top:4151px" width="390" height="417" viewBox="0 0 390 417"><path d="M0 0 H 150 C 300 10 400 120 380 250 C 360 360 260 410 130 412 L 0 410 Z" fill="#f0901e"/></svg>
<p class="abs" style="left:75px;top:4272px;font-size:42px;font-weight:500;letter-spacing:1px;color:#fff;line-height:1">VORNAQUILL</p>
<p class="abs" style="left:94px;top:4330px;font-size:8px;letter-spacing:5px;color:#fff">LEARNING CENTRE</p>
<svg class="abs" style="left:84px;top:4361px" width="190" height="44" viewBox="0 0 190 44" fill="none" stroke="#fff" stroke-width="1.6"><circle cx="22" cy="22" r="19"/><circle cx="70" cy="22" r="19"/><circle cx="118" cy="22" r="19"/><circle cx="166" cy="22" r="19"/></svg>
<div class="fcol">
  <h5 style="left:443px;top:4217px">Site<span class="accent">map</span></h5>
  <ul><li style="left:440px;top:4266px">Home</li><li style="left:440px;top:4297px">Blogs</li><li style="left:440px;top:4329px">Courses</li><li style="left:440px;top:4360px">About Us</li><li style="left:440px;top:4392px">Contact Us</li></ul>
  <h5 style="left:656px;top:4217px">Quick <span class="accent">Links</span></h5>
  <ul><li style="left:655px;top:4266px">Faq</li><li style="left:655px;top:4297px">Terms of Service</li><li style="left:655px;top:4329px">Honor Code</li><li style="left:655px;top:4360px">Privacy Policy</li></ul>
  <h5 style="left:891px;top:4217px">Contact <span class="accent">Us</span></h5>
</div>
<svg class="abs" style="left:888px;top:4266px" width="16" height="22" viewBox="0 0 16 22"><path d="M8 0a8 8 0 0 1 8 8c0 6-8 14-8 14S0 14 0 8a8 8 0 0 1 8-8z" fill="#f0901e"/><circle cx="8" cy="8" r="3" fill="#fff"/></svg>
<p class="abs" style="left:920px;top:4265px;font-size:14px;line-height:27px;color:#555">Corvale<br>418 Linden Row, Fairbrook,<br>TX 75000, USA</p>
<svg class="abs" style="left:888px;top:4357px" width="18" height="18" viewBox="0 0 18 18"><path d="M3 1l4 1 1 4-2 2c1 2 3 4 5 5l2-2 4 1 1 4-2 2C8 18 0 10 1 3z" fill="#f0901e"/></svg>
<p class="abs" style="left:920px;top:4355px;font-size:14px;color:#555">+1 (800) 555 01 42</p>
<svg class="abs" style="left:888px;top:4396px" width="18" height="13" viewBox="0 0 18 13"><rect width="18" height="13" fill="#f0901e"/><path d="M0 0l9 7 9-7" stroke="#fff" fill="none"/></svg>
<p class="abs" style="left:920px;top:4391px;font-size:14px;line-height:27px;color:#555">support@study.vornaquill<br>.com</p>
<div class="abs" style="left:300px;top:4506px;width:490px;height:1px;background:#ddd"></div>
<p class="abs" style="left:0;width:1200px;text-align:center;top:4525px;font-size:13px;color:#555"><span class="accent" style="font-weight:600">©VORNAQUILL LEARNING CENTER</span> - 2020 All rights reserved.</p>

</body>
</html>
```